Wordpress website re-design

Update existing 5 page wordpress website to look more professional. We run a 10 week boxing program that ends in a black tie gala event.

We would like to keep the existing pink hero colour.

The website:
- must be Wordpress
- prefer it to work with the Elementor plugin for easy future changes
- Keep the existing URL structure
- Use white space/backgrounds - D not want all black background or the pink colour used as the background for an entire section
- Shouldn't look too 'templatey'. Good flow between sections

Logo, images and video to use can be found here: https://files.qorvanshare.net/folders/8kq3ZtLmWpe2RxvBn7HsYcDa4-Tu?usp=sharing

Website to be redesigned: https://punchforpurpose-example.com.au/

Target Market(s)

Men working office jobs aged 28-38

Coding

Coded - Design and coding required

Number of Pages Required

5+ page

Colors

Designer to choose colors to be used in the design.

Requirements
Must have
• Wordpress
Nice to have
• Work with Elementor so that I can easily make changes in the future
Should not have
• Entirely black background. Want it to be lighter / plenty of white background. Not too blocky - flowing through sections and some of the images with backgrounds removed to make it less blocky also. I do not want it to be clerly 'templatey'. The pink should be used as a hero colour, not for entire sections

```html
<!DOCTYPE html>
<html lang="en">
<head>
<meta charset="utf-8">
<title>Punch For Purpose – From Desk To The Ring In 10 Weeks</title>
<link rel="stylesheet" href="https://fonts.googleapis.com/css2?family=Crimson+Text:wght@400;600&family=Poppins:wght@300;400;500;600&display=swap">
<style>
:root{
  --pink:#f9bccd;
  --pink-deep:#f08aaa;
  --black:#000;
  --white:#fff;
  --ink:#1a1a1a;
  --soft:#fdf3f6;
  --serif:"Crimson Text", Georgia, serif;
  --sans:"Poppins", Arial, sans-serif;
}
*{margin:0;padding:0;box-sizing:border-box}
html,body{width:1200px;height:4323px;overflow:hidden}
body{position:relative;background:var(--white);font-family:var(--serif);color:var(--ink)}
.abs{position:absolute}

/* header */
.site-header{position:absolute;left:0;top:0;width:1200px;height:109px;background:var(--white)}
.brand{position:absolute;display:flex;align-items:center;gap:8px;font-family:var(--sans);font-weight:600;color:var(--black);line-height:1.15}
.brand .dot{width:12px;height:12px;border-radius:50%;background:var(--pink-deep)}
.brand .name{font-size:15px;width:98px;text-transform:uppercase;text-align:center;letter-spacing:1px}
.main-nav{position:absolute;left:263px;top:44px;display:flex;gap:22px;font-family:var(--sans);font-weight:600;font-size:15px;color:var(--black);text-transform:uppercase}
.main-nav .active{color:var(--pink);position:relative}
.main-nav .active::after{content:"";position:absolute;left:0;right:0;bottom:-10px;height:3px;background:var(--pink)}
.header-join{position:absolute;right:0;top:0;width:243px;height:109px;background:var(--pink);clip-path:polygon(18% 0,100% 0,100% 100%,0 100%);display:flex;align-items:center;justify-content:center;padding-left:40px;font-family:var(--sans);font-weight:600;font-size:18px;color:var(--white)}

/* hero */
.hero{position:absolute;left:0;top:109px;width:1200px;height:571px;background:var(--black)}
.hero-photo{position:absolute;left:67px;top:0;width:655px;height:571px;background:linear-gradient(160deg,#2a0a0a 0%,#7a1416 45%,#c2262a 70%,#2a0505 100%)}
.hero-copy{position:absolute;left:738px;top:72px;width:450px;color:var(--white);font-family:var(--sans);font-weight:300}
.hero-copy h1{font-family:var(--serif);font-weight:400;font-size:29px;line-height:1.2;margin-bottom:8px;white-space:nowrap}
.hero-copy h2{font-family:var(--serif);font-weight:400;font-size:27px;margin:12px 0 4px}
.hero-copy p{font-size:13px;line-height:25px;width:370px}
.btn{position:absolute;display:flex;align-items:center;justify-content:center;font-family:var(--sans);font-weight:600;text-transform:uppercase}
.btn-pink{background:var(--pink);color:var(--white);border-radius:12px}
.btn-dark{background:var(--black);color:var(--white);border-radius:22px}

/* about – light */
.about{position:absolute;left:0;top:680px;width:1200px;height:857px;background:var(--white);color:var(--ink)}
.section-title{position:absolute;left:0;width:1200px;text-align:center;font-family:var(--serif);font-weight:400}
.section-sub{position:absolute;left:0;width:1200px;text-align:center;font-family:var(--serif);color:var(--pink-deep)}
.framed{position:absolute;background:var(--pink);border-radius:16px;padding:14px}
.framed .inner{width:100%;height:100%;background:var(--white);border-radius:10px;padding:10px}
.framed .ph{width:100%;height:100%}
.about-text{position:absolute;font-size:13px;line-height:25px;color:var(--ink)}
.about-text p{margin-bottom:10px}

/* included */
.included-title{top:1572px;font-size:33px;color:var(--black)}
.card{position:absolute;width:323px;height:346px;background:var(--black);border-radius:4px 4px 4px 110px;color:var(--white);padding:0 36px}
.card-head{display:flex;align-items:center;gap:10px;margin:26px 0 20px -8px;height:70px}
.card-icon{width:62px;height:62px;border-radius:50%;background:#f1eefb;display:flex;align-items:center;justify-content:center;flex:none}
.card-head h3{font-family:var(--sans);font-weight:500;font-size:15px;line-height:22px;color:var(--pink)}
.card p{font-size:16px;line-height:25px}

/* team */
.team-bg{position:absolute;left:0;top:2400px;width:1200px;height:780px}
.team-title{top:2500px;font-size:30px;color:var(--white)}
.team-sub{top:2545px;font-size:17px}
.member{position:absolute;top:2606px;width:332px;height:490px;background:var(--white);border-radius:14px;overflow:hidden}
.member .ph{height:277px}
.member .meta{display:flex;justify-content:space-between;align-items:baseline;padding:10px 18px 6px 20px}
.member .meta strong{font-weight:400;font-size:17px}
.member .meta span{font-size:13px}
.member .bio{padding:0 14px 0 20px;font-size:12.5px;line-height:19px}
.member .bio p{margin-bottom:6px}
.arrow{position:absolute;top:2858px;width:44px;height:44px;border-radius:50%;background:var(--pink);display:flex;align-items:center;justify-content:center}

/* fighters */
.fighters-title{top:3210px;font-size:33px;color:var(--black)}
.fighter{position:absolute;top:3331px;height:294px;border-radius:60px 60px 6px 6px;background:linear-gradient(180deg,#e7d2c4 0%,#c7a48d 22%,#1b1b1b 38%,#050505 100%)}
.scrollbar{position:absolute;left:163px;top:3641px;width:903px;height:8px;background:var(--black);border-radius:4px}
.scrollbar span{display:block;width:122px;height:100%;background:var(--pink);border-radius:4px}

/* questions */
.questions-band{position:absolute;left:0;top:3767px;width:1200px;height:252px;background:var(--pink)}
.questions-photo{position:absolute;left:601px;top:3687px;width:599px;height:287px;clip-path:polygon(13% 0,100% 0,100% 100%,4% 100%,0 52%);background:linear-gradient(120deg,#0a0a0a 0%,#8e1518 40%,#d3282b 62%,#1d2a6b 85%,#0d0d0d 100%)}
.questions h2{position:absolute;left:213px;top:3820px;font-family:var(--serif);font-weight:400;font-size:33px;color:var(--black)}
.questions p{position:absolute;left:232px;top:3873px;font-family:var(--serif);font-size:13px;color:var(--white)}

/* footer */
.footer-rule{position:absolute;left:101px;top:4187px;width:1006px;height:1px;background:var(--ink)}
.follow{position:absolute;left:101px;top:4226px;display:flex;align-items:center;gap:14px;font-family:var(--sans);font-size:15px;color:var(--ink)}
.follow .social{display:flex;align-items:center;gap:5px;font-weight:500;font-size:13px}
.follow .social i{width:10px;height:10px;background:var(--ink);display:block}
.copyright{position:absolute;right:96px;top:4230px;font-family:var(--sans);font-size:15px;color:var(--ink)}
</style>
</head>
<body>

<header class="site-header">
  <div class="brand" style="left:50px;top:30px"><span class="name">Punch For Purpose</span><span class="dot"></span></div>
  <nav class="main-nav">
    <span class="active">Home</span><span>About The Program</span><span>Meet The Team</span><span>Past Fighters</span><span>Contact Us</span>
  </nav>
  <div class="header-join">Join Now</div>
</header>

<section class="hero">
  <div class="hero-photo" role="img" aria-label="Female boxer in red headgear and red gloves in a guard stance beside the ring corner"></div>
  <svg class="abs" style="left:0;top:0" width="1200" height="571" aria-hidden="true">
    <polygon points="0,571 0,500 1200,420 1200,571" fill="#fff"/>
    <polygon points="826,523 1200,450 1200,571 935,571" fill="#f9bccd"/>
  </svg>
  <div class="hero-copy">
    <h1>From Desk To The Ring In 10 Weeks!</h1>
    <p>We help people like you go from little or no boxing experience to a boxing bout in 10 weeks. Get fit, have fun and support charity in a safe environment.</p>
    <h2>Upcoming intakes:</h2>
    <p>13 February 2024 – Event 20 April 2024 (Riverside Music Hall day event)</p>
    <p style="margin-top:3px">2 April 2024 – Event 15 June 2024 (Grand Regent Convention Centre night event)</p>
  </div>
  <div class="btn btn-pink" style="left:738px;top:406px;width:170px;height:45px;font-size:15px">Join Now</div>
</section>

<section class="about">
  <svg class="abs" style="left:0;top:0" width="1200" height="857" aria-hidden="true">
    <polygon points="0,755 0,857 218,857 330,762" fill="#f9bccd"/>
  </svg>
  <h2 class="section-title" style="top:15px;font-size:28px;color:#000">What Is Punch For Purpose?</h2>
  <p class="section-sub" style="top:55px;font-size:13px">10 Weeks, 30 Training Sessions, 1 Fight Night</p>

  <div class="framed" style="left:129px;top:97px;width:400px;height:347px">
    <div class="inner"><div class="ph" role="img" aria-label="Fighter walking out to the ring through a crowd with sparkler fountains" style="background:linear-gradient(180deg,#1c2a3a 0%,#3a3a4a 40%,#6a1a1a 75%,#1a1414 100%)"></div></div>
  </div>
  <div class="about-text" style="left:564px;top:115px;width:465px">
    <p>Raising much needed funds for charity, Punch For Purpose puts you through your paces with fellow beginners to intermediates over a 10 Week program to prepare you for your big moment, as you Punch For Purpose! Make long-lasting friendships training all together as a group over 10 weeks, as our world-class trainers get you ring ready for the big event finale. Each participant will be matched up with an opponent they will get to know throughout the program, based on Height, Weight &amp; Ability which will be assessed over the 10 weeks by trainers &amp; PFP staff</p>
    <p>Our boxing facilities are within 10 mins of Brisbane's CBD, making it easy to attend sessions straight from work. Sessions are 45 minutes in duration, with one session every Tuesday &amp; Thursday (evenings), as well as a Saturday morning session @ 10am.</p>
  </div>

  <div class="about-text" style="left:129px;top:535px;width:460px">
    <p>Punch For Purpose is for both Women and Men aged 18+, with matchups taking place only days out from the Main Event.. featuring YOU!</p>
    <p>The cost is $895 which includes 10 weeks of training, 3x sessions per week, also includes your own Boxing Gloves, Headgear and everything you'll need to make the leap from Desk to the Ring at the Black tie boxing event!</p>
    <p>Spots are strictly limited, so what are you waiting for!</p>
  </div>
  <div class="framed" style="left:607px;top:470px;width:400px;height:345px">
    <div class="inner"><div class="ph" role="img" aria-label="Two boxers in red and blue exchanging punches in the ring" style="background:linear-gradient(100deg,#0a0a0a 0%,#b32024 35%,#d8d0c8 55%,#2a3fa0 80%,#0a0a0a 100%)"></div></div>
  </div>
</section>

<h2 class="section-title included-title">What's Included?</h2>

<div class="card" style="left:96px;top:1636px">
  <div class="card-head"><div class="card-icon"><svg width="34" height="34" viewBox="0 0 34 34" fill="none" stroke="#5b4fd6" stroke-width="2"><rect x="5" y="7" width="24" height="22" rx="2"/><line x1="5" y1="13" x2="29" y2="13"/><line x1="11" y1="4" x2="11" y2="10"/><line x1="23" y1="4" x2="23" y2="10"/></svg></div><h3>3 Weekly Training Sessions For 10 Weeks</h3></div>
  <p>Training takes place each Tuesday, Thursday and Saturday throughout the 10 week program.</p>
</div>
<div class="card" style="left:443px;top:1636px">
  <div class="card-head"><div class="card-icon"><svg width="34" height="34" viewBox="0 0 34 34" fill="none" stroke="#5b4fd6" stroke-width="2"><rect x="5" y="19" width="5" height="11"/><rect x="13" y="14" width="5" height="16"/><rect x="21" y="9" width="5" height="21"/><polyline points="4,14 12,8 19,10 29,3"/></svg></div><h3>Fight Kit</h3></div>
  <p>We provide a full fight kit so that you're ready to train from day 1. This includes boxing gloves, wraps and head gear. All you need to provide is a personal mouth guardm suitable footwear and groin protection suited to your individual needs.</p>
</div>
<div class="card" style="left:792px;top:1636px">
  <div class="card-head"><div class="card-icon"><svg width="34" height="34" viewBox="0 0 34 34" fill="none" stroke="#5b4fd6" stroke-width="2"><circle cx="15" cy="15" r="10"/><path d="M18 11h-4a2 2 0 0 0 0 4h2a2 2 0 0 1 0 4h-4M15 9v2M15 19v2"/><line x1="23" y1="23" x2="31" y2="31"/></svg></div><h3>Membership To Stronghold Boxing</h3></div>
  <p>All Punch For Purpose fighters receive full membership to Stronghold Boxing for the duration of the program. This means you can attend additional classes as you desire at no extra cost.</p>
</div>
<div class="card" style="left:96px;top:2029px">
  <div class="card-head"><div class="card-icon"><svg width="34" height="34" viewBox="0 0 34 34" fill="none" stroke="#5b4fd6" stroke-width="2"><path d="M17 4a9 9 0 0 0-5 16.5V25h10v-4.5A9 9 0 0 0 17 4z"/><line x1="13" y1="29" x2="21" y2="29"/></svg></div><h3>Black Tie Fight Event</h3></div>
  <p>Experience the glory of fighting in front of your friends, family and co-workers while they sit down to a two course black tie gala event.</p>
</div>
<div class="card" style="left:443px;top:2029px">
  <div class="card-head"><div class="card-icon"><svg width="34" height="34" viewBox="0 0 34 34" fill="none" stroke="#5b4fd6" stroke-width="2"><rect x="4" y="7" width="26" height="20" rx="2"/><circle cx="12" cy="14" r="2.5"/><polyline points="5,25 13,18 19,23 24,19 30,24"/></svg></div><h3>World Class Trainers</h3></div>
  <p>Be trained by the best of the best, including active professional boxers.</p>
</div>
<div class="card" style="left:792px;top:2029px">
  <div class="card-head"><div class="card-icon"><svg width="34" height="34" viewBox="0 0 34 34" fill="none" stroke="#5b4fd6" stroke-width="2"><rect x="7" y="4" width="20" height="26" rx="2"/><line x1="11" y1="11" x2="23" y2="11"/><line x1="11" y1="16" x2="23" y2="16"/><line x1="11" y1="21" x2="19" y2="21"/></svg></div><h3>Fair Matchmaking</h3></div>
  <p>Our experienced trainers will ensure you are matched with someone of a comparable skill level and size.Our goal is to ensure all fighters have a good time, go the full 3 rounds and most importantly, don't get hurt.</p>
</div>

<svg class="team-bg" width="1200" height="780" viewBox="0 0 1200 780" aria-hidden="true">
  <polygon points="0,112 1200,0 1200,780 275,780 0,712" fill="#000"/>
  <polygon points="0,712 210,712 275,780 0,780" fill="#f9bccd"/>
</svg>
<h2 class="section-title team-title">Meet Our Amazing Team</h2>
<p class="section-sub team-sub">The Faces Behind The Success</p>

<article class="member" style="left:89px">
  <div class="ph" role="img" aria-label="Two boxers in blue and red trading punches at close range" style="background:linear-gradient(120deg,#1a1a1a 0%,#b5262a 45%,#2b45b0 75%,#111 100%)"></div>
  <div class="meta"><strong>Liam Harcourt</strong><span>Director</span></div>
  <div class="bio"><p>A property developer and lawyer by day, Liam is a testament of working hard to achieve your goals. Brisbane born and bred, Liam developed a passion for boxing and hasn't looked back. Already an advocate and supporter of boxing through sponsorships of professional Australian boxing athletes, Liam has now decided to support everyday people jumping in the ring and getting fit, all for a good cause.</p></div>
</article>
<article class="member" style="left:435px">
  <div class="ph" role="img" aria-label="Head trainer in a black shirt talking to a boxer in red headgear in the corner" style="background:linear-gradient(100deg,#0c0c0c 0%,#2a2a2a 45%,#c0262a 70%,#111 100%)"></div>
  <div class="meta"><strong>Declan Rowe</strong><span>Head Trainer</span></div>
  <div class="bio"><p>From a young age, Rowe knew that he wanted to become a professional boxer and become a world champion and within four months and four fights of his professional career, the 24-year old won state honours by winning the Queensland State Light Heavyweight Title and eight months later he added to the honours list by winning the Australian Light Heavyweight Title when beating Trent Ashby.</p></div>
</article>
<article class="member" style="left:780px">
  <div class="ph" role="img" aria-label="Boxer in blue sparring with a boxer in a red vest under arena lights" style="background:linear-gradient(110deg,#1a1a1a 0%,#283f9e 35%,#c62a2e 65%,#161616 100%)"></div>
  <div class="meta"><strong>Marcus Vale</strong><span>Trainer</span></div>
  <div class="bio"><p>'Banging' Marcus Vale is a member of the Stronghold boxing Pro Team andcurrent Australasian Welterweight Champion.</p><p>NBFA QLD Aus and Australasian ChampionWPBA Asia Pacific ChampionIPBA Pan Pacific Champion</p><p>When Marcus isn't training the house down, he is coaching classes and destroying Stronghold members with his epic workout routines</p></div>
</article>
<div class="arrow" style="left:37px"><svg width="24" height="24" viewBox="0 0 24 24"><circle cx="12" cy="12" r="11" fill="#000"/><path d="M17 12H8M11 8l-4 4 4 4" stroke="#fff" stroke-width="2.4" fill="none"/></svg></div>
<div class="arrow" style="left:1121px"><svg width="24" height="24" viewBox="0 0 24 24"><circle cx="12" cy="12" r="11" fill="#000"/><path d="M7 12h9M13 8l4 4-4 4" stroke="#fff" stroke-width="2.4" fill="none"/></svg></div>

<h2 class="section-title fighters-title">Meet some of the previous Fighters</h2>
<div class="fighter" role="img" aria-label="Past fighter in a black team shirt with arms crossed" style="left:131px;width:196px"></div>
<div class="fighter" role="img" aria-label="Past fighter in a black team shirt with arms crossed" style="left:389px;width:198px"></div>
<div class="fighter" role="img" aria-label="Past fighter in a black team shirt with arms crossed" style="left:651px;width:196px"></div>
<div class="fighter" role="img" aria-label="Past fighter in a black team shirt with arms crossed" style="left:876px;width:203px"></div>
<div class="scrollbar"><span></span></div>

<section class="questions">
  <div class="questions-band"></div>
  <div class="questions-photo" role="img" aria-label="Boxer in red headgear throwing a punch at an opponent in blue"></div>
  <h2>Got Any Questions?</h2>
  <p>Drop Us A Line And Keep In Touch</p>
  <div class="btn btn-dark" style="left:232px;top:3913px;width:171px;height:44px;font-size:15px">Contact Us</div>
</section>

<footer>
  <div class="brand" style="left:101px;top:4100px"><span class="name">Punch For Purpose</span><span class="dot"></span></div>
  <div class="btn btn-pink" style="left:935px;top:4100px;width:171px;height:45px;font-size:15px;border-radius:6px">Join Now</div>
  <div class="footer-rule"></div>
  <div class="follow">Follow Us
    <span class="social"><i></i>Chatter</span>
    <span class="social"><i></i>Snapgrid</span>
    <span class="social"><i></i>Clipstream</span>
  </div>
  <div class="copyright">© 2023 All Rights Reserved</div>
</footer>

</body>
</html>
```